July 2022 Industrial Manufacturer Product Expo Mexico City

We manufacture large screws and fastners for large Mining equipment, Trains, large ships, airplanes, wind turbines, and so on. We also do custom work base on the customer needs. No matter the size we can make it.
We have a Expo coming up with companies all over the world. We have to stand out we are a family own business so our customer service will be above and beyond anyone can provide. We do not have a sales force to push our products and services we provide one on one service.
Plus@!! I'm looking for anything that you designers can come up with if it was your company to put on a business card, plus i want to do a 1 or 2 sided pamphlet, and then a website. We make Speciality Bolts for large mining equipment these bolts can be 3 to 4 foot long!!! Plus fasteners, Nuts, washers, any, size, strengths, special materials, we offer more of a ono on one customer service, We are a small company, family own, but can fulfill any type of orders. We can also provide special time lines for emergency orders. "We keep the machines running we here at KRV don't believe in down time" We want to hear any slogan based on our company to stand out.
Thanks i really appreciate all your work and options that we have to pick on. Plus just a thought we could possibly want to entertain a experience Marketing internet help maybe a employment possibility. Thanks

I need 2 cards one in Spanish and English Like the steel back ground maybe send me in some bright red and blue writing Same with the Black cards Please remove the word Military The logo KRV maybe integrate a picture of a Bolt 🔩 Thank you

Still looking for I need 2 cards one in Spanish and English Like the steel back ground maybe send me in some bright red and blue writing Same with the Black cards try bright writing Please remove the word Military The logo KRV maybe integrate a picture of a Bolt 🔩 Plus will need the company to make a brochure and website next Thank you

Target Market(s)

Large Mining, Ship, Train, Green Energy, VELM, and Government equipment. Throughout the World

Industry/Entity Type

We can Custom Manufacture any type of Fastners for Mining equipment, Trains, Ships, Green energy, Governments, or military projects. wind turbines,

Contact Information for Business Card

I attached the name and contact info that's on a card, plus the Company Logo. Would like industrial looking background with Bright Colors that will stand out!! If we can insert somewhere maybe on back that we "Custom Manufacture Any Size or Quantity Fastners for Large Mining Equipment, Trains, Ships, Green Energy Equipment or Government Projects

Font styles to use
Other font styles liked:
• You Pick, has to be bold, colorful standout, Professional looking Beable to read it.

Colors

Designer to choose colors to be used in the design.

Requirements
Must have
• Need in Spanish and English TO STANDOUT FROM THE REST OF THE EXPO!! See Business card details, Rounded corners
Nice to have
• Can i see some of the darker cards with Bright Red and Blue letters I like to see the different type of card material, heavy thickness, plastic, transparent, Metal types, Bright Colors, I saw like Raised letters like on the logo.

```html
<!DOCTYPE html>
<html lang="es">
<head>
<meta charset="utf-8">
<title>KRV – Tarjetas de presentación</title>
<link rel="stylesheet" href="https://fonts.googleapis.com/css2?family=Roboto+Condensed:wght@400;700&family=Roboto:wght@400;500;700&display=swap">
<style>
  :root {
    --bg: #bdbdbd;
    --card-white: #ffffff;
    --card-black-top: #3a3b3f;
    --card-black-bottom: #0b0b0c;
    --edge-blue: #1e8fd6;
    --ink-navy: #1b2a8f;
    --ink-blue: #1f74c7;
    --ink-grey: #555a60;
    --ink-dark: #3b3d40;
    --silver: #d9dadc;
  }
  * { box-sizing: border-box; margin: 0; padding: 0; }
  html, body { width: 1200px; height: 800px; overflow: hidden; }
  body {
    background: linear-gradient(160deg, #d6d6d6 0%, var(--bg) 100%);
    font-family: "Roboto", Arial, sans-serif;
    position: relative;
  }
  .card {
    position: absolute;
    width: 540px;
    height: 310px;
    border-radius: 22px;
    box-shadow: 0 3px 0 var(--edge-blue), 0 14px 30px rgba(0,0,0,0.25);
    overflow: hidden;
  }
  .card--front { left: 40px; top: 245px; background: var(--card-white); }
  .card--back {
    left: 620px; top: 245px;
    background: linear-gradient(150deg, var(--card-black-top) 0%, #1d1e20 55%, var(--card-black-bottom) 100%);
  }

  /* Brand block */
  .brand { position: absolute; text-align: center; }
  .brand__name {
    font-family: "Roboto", Arial, sans-serif;
    font-weight: 700;
    line-height: 1;
    letter-spacing: 6px;
  }
  .brand__tagline {
    font-family: "Roboto Condensed", Arial, sans-serif;
    font-weight: 400;
    text-transform: uppercase;
    white-space: nowrap;
  }
  .card--front .brand { right: 70px; top: 38px; }
  .card--front .brand__name { font-size: 62px; color: var(--ink-dark); }
  .card--front .brand__tagline { font-size: 11px; color: var(--ink-navy); margin-top: 6px; letter-spacing: 0.5px; }

  .card--back .brand { left: 0; right: 0; top: 88px; }
  .card--back .brand__name { font-size: 96px; color: var(--silver); letter-spacing: 10px; }
  .card--back .brand__tagline { font-size: 17px; color: var(--silver); margin-top: 12px; letter-spacing: 1px; }

  /* Front details */
  .divider {
    position: absolute;
    left: 120px; right: 40px; top: 186px;
    height: 1px;
    background: linear-gradient(90deg, var(--edge-blue), var(--ink-navy));
  }
  .person { position: absolute; left: 40px; top: 140px; }
  .person__name {
    font-family: "Roboto Condensed", Arial, sans-serif;
    font-weight: 700;
    font-size: 21px;
    color: var(--ink-blue);
  }
  .person__title-prefix { color: var(--ink-navy); }
  .person__role {
    font-family: "Roboto Condensed", Arial, sans-serif;
    font-size: 13px;
    color: var(--ink-grey);
    margin-top: 2px;
  }
  .contact-rule {
    position: absolute; left: 40px; top: 204px; width: 150px; height: 1px;
    background: var(--ink-navy);
  }
  .contacts { position: absolute; left: 40px; top: 214px; list-style: none; }
  .contacts__item {
    display: flex; align-items: center; gap: 8px;
    font-family: "Roboto Condensed", Arial, sans-serif;
    font-size: 14px; color: var(--ink-grey);
    height: 19px;
  }
  .contacts__icon { width: 12px; height: 12px; flex: none; }
</style>
</head>
<body>

  <section class="card card--front" aria-label="Frente de tarjeta">
    <div class="brand">
      <div class="brand__name">KRV</div>
      <div class="brand__tagline">Fabricacion y distribucion de tornillos</div>
    </div>

    <div class="divider"></div>

    <div class="person">
      <div class="person__name"><span class="person__title-prefix">Lic.</span> Mariela Ortega Ruiz</div>
      <div class="person__role">Cotizaciones en</div>
    </div>

    <div class="contact-rule"></div>

    <ul class="contacts">
      <li class="contacts__item">
        <svg class="contacts__icon" viewBox="0 0 12 12" aria-hidden="true">
          <path d="M2.5 1 L4.5 1 L5 3.5 L3.8 4.4 C4.5 6 6 7.5 7.6 8.2 L8.5 7 L11 7.5 L11 9.5 C11 10.4 10.3 11 9.4 11 C4.8 10.6 1.4 7.2 1 2.6 C1 1.7 1.6 1 2.5 1 Z" fill="var(--ink-navy)"/>
        </svg>
        <span>5550192834</span>
      </li>
      <li class="contacts__item">
        <svg class="contacts__icon" viewBox="0 0 12 12" aria-hidden="true">
          <rect x="1.5" y="1.5" width="9" height="9" fill="none" stroke="var(--ink-navy)" stroke-width="1.3"/>
        </svg>
        <span>5550176420</span>
      </li>
      <li class="contacts__item">
        <svg class="contacts__icon" viewBox="0 0 12 12" aria-hidden="true">
          <rect x="0.5" y="2" width="11" height="8" fill="var(--ink-navy)"/>
          <path d="M0.8 2.4 L6 6.6 L11.2 2.4" fill="none" stroke="#ffffff" stroke-width="1"/>
        </svg>
        <span>krv.ventas@correo.mx</span>
      </li>
    </ul>
  </section>

  <section class="card card--back" aria-label="Reverso de tarjeta">
    <div class="brand">
      <div class="brand__name">KRV</div>
      <div class="brand__tagline">Fabricacion y distribucion de tornillos</div>
    </div>
  </section>

</body>
</html>
```